Business card for law firm

Need business card for new law firm. Think confident, authoritative, conservative, but not stuffy or old-fashioned.

Contact Information for Business Card

Content for card - logo (uploaded), plus the following:

Paul Whitcombe (larger font)
Managing Partner (larger font, but not as large as name)
Level 9, 7 Ferris Lane
Sydney NSW 2000
Main Tel 02 9364 2710
Direct Tel 02 8472 3159
Email paul@qvlegal.com.au
www.qvlegal.com.au

Letterhead design should include logo plus:
Level 9, 7 Ferris Lane
Sydney NSW 2000
Tel 02 8472 3159
www.qvlegal.com.au

```html
<!DOCTYPE html>
<html lang="en">
<head>
<meta charset="utf-8">
<title>Quayview Legal – Business Card</title>
<link href="https://fonts.googleapis.com/css2?family=Open+Sans:wght@400;600;700&display=swap" rel="stylesheet">
<style>
  :root {
    --backdrop: #3a322e;
    --card: #1c1e20;
    --card-edge: #151617;
    --ink: #ffffff;
    --silver: #c9cbcd;
    --muted: #9a9c9f;
  }
  * { margin: 0; padding: 0; box-sizing: border-box; }
  html, body {
    width: 1200px; height: 864px; overflow: hidden;
    background: var(--backdrop);
    font-family: "Open Sans", Arial, sans-serif;
  }
  .canvas {
    width: 1200px; height: 864px;
    display: flex; align-items: center; justify-content: center; gap: 40px;
  }
  .card {
    width: 540px; height: 330px;
    background: var(--card);
    border: 1px solid var(--card-edge);
    box-shadow: 0 14px 30px rgba(0,0,0,.35);
    position: relative;
    color: var(--ink);
  }

  /* Front */
  .card--front {
    display: flex; flex-direction: column; align-items: center; justify-content: center;
  }
  .front-mark {
    width: 54px; height: 54px; background: var(--silver); margin-bottom: 18px;
  }
  .front-name {
    font-size: 30px; font-weight: 400; letter-spacing: 3px;
    color: var(--silver); text-transform: uppercase;
  }
  .front-web {
    margin-top: 34px; font-size: 14px; letter-spacing: 7px; color: var(--silver);
  }

  /* Back */
  .card--back { display: flex; align-items: center; padding: 0 36px 0 44px; }
  .back-brand {
    width: 190px; display: flex; flex-direction: column; align-items: center;
  }
  .back-mark { width: 130px; height: 130px; background: var(--ink); }
  .back-name {
    margin-top: 14px; font-size: 13px; font-weight: 600; letter-spacing: 2px;
    text-transform: uppercase; color: var(--ink);
  }
  .divider {
    width: 2px; height: 210px; margin: 0 24px 0 18px;
    background: linear-gradient(to bottom, rgba(255,255,255,.15), #fff 40%, rgba(255,255,255,.1));
  }
  .details { flex: 1; }
  .person-name { font-size: 21px; font-weight: 700; text-transform: uppercase; line-height: 1.1; }
  .person-title { font-size: 13px; font-weight: 700; text-transform: uppercase; margin-bottom: 10px; }
  .address { font-size: 14px; line-height: 1.3; margin-bottom: 4px; }
  .contact { list-style: none; font-size: 14px; line-height: 1.35; }
  .contact li { display: flex; align-items: center; }
  .contact svg { width: 13px; height: 13px; margin-right: 10px; fill: var(--ink); flex: none; }
</style>
</head>
<body>
<main class="canvas">
  <section class="card card--front" aria-label="Card front">
    <div class="front-mark"></div>
    <div class="front-name">Quayview Legal</div>
    <div class="front-web">www.qvlegal.com.au</div>
  </section>

  <section class="card card--back" aria-label="Card back">
    <div class="back-brand">
      <div class="back-mark"></div>
      <div class="back-name">Quayview Legal</div>
    </div>
    <div class="divider"></div>
    <div class="details">
      <div class="person-name">Paul Whitcombe</div>
      <div class="person-title">Managing Partner</div>
      <div class="address">Level 9, 7 Ferris Lane<br>Sydney NSW 2000</div>
      <ul class="contact">
        <li><svg viewBox="0 0 16 16"><path d="M2 5c0-2 3-3 6-3s6 1 6 3v1h-3V5H5v1H2zM3 8h10l1 6H2z"/></svg>02 9364 2710</li>
        <li><svg viewBox="0 0 16 16"><path d="M4 1h8v14H4zM5.5 3v9h5V3z"/></svg>02 8472 3159</li>
        <li><svg viewBox="0 0 16 16"><path d="M1 3h14v10H1zM2 4l6 5 6-5z"/></svg>paul@qvlegal.com.au</li>
        <li><svg viewBox="0 0 16 16"><circle cx="8" cy="8" r="7"/></svg>www.qvlegal.com.au</li>
      </ul>
    </div>
  </section>
</main>
</body>
</html>
```